Design a New Business Card for Our Company

We are looking for fresh, unique, and a modern business card that reflects our roots as digital marketing agency focused on SEM.

Industry/Entity Type

Marketing

Contact Information for Business Card

looking for very unique out of the box designs. clean and modern that compliments our logo

Requirements
Must have
• colors should match our logo
• Front should have name, address, email, and phone/fax of the person, phone/fax are the same number
• back should have our url

```html
<!DOCTYPE html>
<html lang="en">
<head>
<meta charset="utf-8">
<title>Tidewell Digital – Business Card</title>
<link href="https://fonts.googleapis.com/css2?family=Roboto:wght@300;400;500&display=swap" rel="stylesheet">
<style>
  :root {
    --backdrop: #b3b1b2;
    --brand-blue: #5b95cf;
    --brand-blue-deep: #4f8bc9;
    --paper: #ffffff;
    --ink-light: #ffffff;
  }
  * { box-sizing: border-box; margin: 0; padding: 0; }
  html, body {
    width: 1200px; height: 1000px; overflow: hidden;
    background: var(--backdrop);
    font-family: "Roboto", Arial, sans-serif;
  }
  .canvas { position: relative; width: 1200px; height: 1000px; }

  .card { position: absolute; background: var(--paper); overflow: hidden; }
  .card--back  { left: 230px; top: 36px;  width: 705px; height: 431px; }
  .card--front { left: 231px; top: 507px; width: 707px; height: 432px; }

  .pattern-band { position: absolute; left: 0; width: 100%; background: var(--brand-blue); }
  .pattern-band--top { top: 0; height: 157px; }
  .pattern-band--bottom { top: 275px; height: 156px; }

  .wordmark {
    position: absolute; left: 0; width: 100%;
    display: flex; align-items: center; justify-content: center; gap: 16px;
  }
  .wordmark__dot { width: 34px; height: 34px; border-radius: 50%; background: var(--brand-blue); }
  .wordmark__name {
    font-weight: 500; font-size: 52px; letter-spacing: -1px;
    color: var(--brand-blue); line-height: 1;
  }
  .card--back .wordmark { top: 157px; height: 118px; }
  .card--front .wordmark { top: 70px; height: 90px; }
  .card--front .wordmark__name { font-size: 50px; }

  .website {
    position: absolute; left: 0; width: 100%; top: 384px;
    text-align: center; color: var(--ink-light);
    font-weight: 500; font-size: 21px;
  }

  .person {
    position: absolute; left: 0; width: 100%; top: 214px;
    display: flex; align-items: flex-end; justify-content: center;
  }
  .person__rule { flex: 1; height: 2px; background: var(--brand-blue); margin-bottom: 1px; }
  .person__name {
    padding: 0 6px; color: var(--brand-blue-deep);
    font-weight: 500; font-size: 25px; line-height: 1;
  }
  .contact-panel {
    position: absolute; left: 0; top: 240px; width: 100%; height: 192px;
    background: var(--brand-blue);
    border-top: 2px solid var(--paper);
    box-shadow: 0 -2px 0 var(--brand-blue);
  }
  .person__title {
    position: absolute; left: 0; width: 100%; top: 0;
    text-align: center; color: var(--ink-light);
    font-weight: 300; font-size: 20px;
  }
  .contact-item {
    position: absolute; top: 50px; width: 170px; margin-left: -85px;
    text-align: center; color: var(--ink-light);
    font-weight: 300; font-size: 16px; line-height: 20px;
  }
  .contact-item svg { display: block; margin: 0 auto 14px; }
  .contact-item--single p { margin-top: 20px; }
  .contact-item--address { left: 101px; }
  .contact-item--phone   { left: 266px; }
  .contact-item--fax     { left: 434px; }
  .contact-item--email   { left: 599px; }
</style>
</head>
<body>
<main class="canvas">

  <section class="card card--back">
    <div class="pattern-band pattern-band--top" role="img" aria-label="Faint repeating brand pattern on blue"></div>
    <div class="wordmark">
      <span class="wordmark__dot"></span>
      <span class="wordmark__name">Tidewell Digital</span>
    </div>
    <div class="pattern-band pattern-band--bottom" role="img" aria-label="Faint repeating brand pattern on blue"></div>
    <p class="website">www.tidewelldigital.com</p>
  </section>

  <section class="card card--front">
    <div class="wordmark">
      <span class="wordmark__dot"></span>
      <span class="wordmark__name">Tidewell Digital</span>
    </div>

    <div class="person">
      <span class="person__rule"></span>
      <span class="person__name">Mark Ellison</span>
      <span class="person__rule"></span>
    </div>

    <div class="contact-panel">
      <p class="person__title">President</p>

      <div class="contact-item contact-item--address">
        <svg width="26" height="26" viewBox="0 0 26 26" fill="none" stroke="#fff" stroke-width="1.6">
          <circle cx="13" cy="13" r="12"/>
          <path d="M13 20c-3-4-5-6.5-5-9a5 5 0 0 1 10 0c0 2.5-2 5-5 9z"/>
          <circle cx="13" cy="11" r="1.8"/>
        </svg>
        <p>4870 Harbor Vale Rd<br>Linden Grove,<br>CA 90417 USA</p>
      </div>

      <div class="contact-item contact-item--single contact-item--phone">
        <svg width="26" height="26" viewBox="0 0 26 26" fill="none" stroke="#fff" stroke-width="1.6">
          <circle cx="13" cy="13" r="12"/>
          <path d="M9 7l2.5 2.5-1.5 2a8 8 0 0 0 4.5 4.5l2-1.5L19 17l-2 2c-5 0-10-5-10-10z" fill="#fff"/>
        </svg>
        <p>888-410-5573</p>
      </div>

      <div class="contact-item contact-item--single contact-item--fax">
        <svg width="26" height="26" viewBox="0 0 26 26" fill="none" stroke="#fff" stroke-width="1.6">
          <circle cx="13" cy="13" r="12"/>
          <rect x="9" y="6.5" width="8" height="4"/>
          <rect x="6.5" y="10.5" width="13" height="6" rx="1" fill="#fff"/>
          <rect x="9" y="14.5" width="8" height="5" fill="#5b95cf"/>
        </svg>
        <p>888-410-5573</p>
      </div>

      <div class="contact-item contact-item--single contact-item--email">
        <svg width="26" height="26" viewBox="0 0 26 26" fill="none" stroke="#fff" stroke-width="1.6">
          <circle cx="13" cy="13" r="12"/>
          <rect x="7" y="8.5" width="12" height="9" fill="#fff"/>
          <path d="M7 8.5l6 5 6-5" stroke="#5b95cf"/>
        </svg>
        <p>hello@tidewell.com</p>
      </div>
    </div>
  </section>

</main>
</body>
</html>
```